High Tech Real Estate Startup needs a business card

We are developing an innovative real estate marketing product based around advanced search and virtual reality.

We talk to people, we need business cards.

Target Market(s)

The target market is technology professionals and realtors.

Contact Information for Business Card

The information to be included will include

Name
Title
Phone Number
E-mail Address
www.zelquin.com

It should use simple iconography for each one of those fields.

Font styles to use
Other font styles liked:
• Co, Jubilat, Avenir

Colors

Designer to choose colors to be used in the design.

Requirements
Must have
• Clean aesthetic,
• Good use of negative space.
• It should use our company logo, shown in the attached file. It is able to use the negative of that logo (coloured font and white background) and I have attached other acceptable accent colours in a swatch file.
Should not have
• Should not be too busy
• No extraneous text (slogans, tag lines etc)

```html
<!DOCTYPE html>
<html lang="en">
<head>
<meta charset="utf-8">
<title>Zelquin Business Card</title>
<link rel="stylesheet" href="https://fonts.googleapis.com/css2?family=Open+Sans:wght@400;600&display=swap">
<style>
  :root {
    --backdrop: #2f2f30;
    --teal: #3caaac;
    --teal-deep: #2a8486;
    --paper: #f3f3f2;
    --ink: #333638;
    --ink-soft: #4a4d50;
    --rule: #5fb8c0;
  }
  * { margin: 0; padding: 0; box-sizing: border-box; }
  html, body {
    width: 799px;
    height: 1200px;
    overflow: hidden;
    background: var(--backdrop);
    font-family: "Open Sans", sans-serif;
  }
  .sheet {
    width: 799px;
    height: 1200px;
    display: flex;
    flex-direction: column;
    align-items: center;
    justify-content: space-around;
    padding: 60px 0;
  }
  .card {
    width: 620px;
    height: 354px;
    border-radius: 30px;
    position: relative;
  }
  .card-front {
    background: var(--teal);
    display: flex;
    align-items: center;
    justify-content: center;
  }
  .brand-name {
    font-weight: 600;
    font-size: 76px;
    letter-spacing: 4px;
    color: var(--teal-deep);
  }
  .card-back {
    background: var(--paper);
    display: flex;
    flex-direction: column;
    align-items: center;
    justify-content: center;
    text-align: center;
  }
  .person-name {
    font-weight: 600;
    font-size: 27px;
    color: var(--ink);
  }
  .divider {
    width: 290px;
    height: 1px;
    background: var(--rule);
    margin: 8px 0 6px;
  }
  .person-title {
    font-size: 14px;
    color: var(--ink-soft);
    margin-bottom: 18px;
  }
  .contact-list {
    list-style: none;
    font-size: 16px;
    line-height: 1.3;
    color: var(--ink);
  }
</style>
</head>
<body>
  <main class="sheet">
    <section class="card card-front" aria-label="Card front">
      <span class="brand-name">ZELQUIN</span>
    </section>
    <section class="card card-back" aria-label="Card back">
      <h1 class="person-name">John Doe Smith</h1>
      <div class="divider"></div>
      <p class="person-title">Managing Director</p>
      <ul class="contact-list">
        <li>555.555.5555</li>
        <li>johndoe@zelquin.com</li>
        <li>www.zelquin.com</li>
      </ul>
    </section>
  </main>
</body>
</html>
```